Flyer, poster, banner and social media titles designs for Community Mending Chartre

The Harbourline Charter for Community Mending provide a nationally agreed framework to guide recovery policy and practice across Australia. The Principles support recovery practitioners, governments, non-government organisations and communities to deliver effective, community-centred recovery outcomes.
The Principles have recently been refreshed through extensive consultation and we require a contemporary visual identity and design suite that will increase awareness, engagement and practical application of the Principles.
The redesign will cover:
• A4 Brochure (primary publication)
• A3 Poster
• Pull up banner
• Social Media Tiles
The new design should:
• Create a recognisable brand for the Harbourline Charter.
• Appeal to both experienced and emerging recovery practitioners.
• Reflect contemporary disaster recovery practice.
• Feel people-focused rather than government-focused.
• Support future resources such as videos, implementation guides, presentations and workshop materials.
• Remain relevant for several years without requiring a major redesign.
Target Audience
• Disaster recovery practitioners
• Government agencies
• Non-government organisations
• Community recovery workers
• Recovery managers and leaders
• Community stakeholders and volunteers
The visual identity should reflect the six Principles:
• Understanding Context
• Recognising Complexity
• Community-Centred Approaches
• Coordination
• Communication
• Capacity Building
The design should communicate:
• Recovery is centred on people and communities.
• Recovery is collaborative and involves many sectors.
• Recovery is adaptive, inclusive and evidence-informed.
• Recovery supports resilience and long-term wellbeing.
• The Principles provide practical guidance for recovery practice.
We are looking for:
• Modern and professional
• Warm and approachable
• Human-centred
• Inclusive and accessible
• Australian in context
• Visually engaging
• Suitable for print and digital use
We would like to avoid:
• Images of disaster destruction
• Emergency response imagery (fire trucks, flashing lights, etc.)
• Overly corporate or bureaucratic designs
• Designs that focus on deficits rather than recovery and growth
Consider themes such as:
• Connection and collaboration
• Communities and people
• Growth, recovery and renewal
Accessibility
Designs should:
• Meet accessibility best practice
• Use clear typography
• Achieve strong colour contrast
• Be suitable for both digital and print formats

Deliverables
1. Principles Brochure
• A4 trifold size x 2 (online and print friendly version)
• A side to include cover side, logos side and overview of principles.
• B side full details of the principles
• Graphic to highlight the 3 c’s concept (RECOVERY Context, complexity, community centred, coordinate, communicate and capacity). Currently 3 circles.
• Can be printed and distributed electronically
2. Poster
• A1 and A3 versions
• Suitable for office and workshop display
3. Pull-Up Banner - 850 mm (W) × 2000 mm (H)
• Conference and event use
• High visual impact
• Strong branding and concise messaging
4. Social Media Tiles x 3

We are providing an extension and increasing the budget following feedback from designers. We are wanting the resources to look and feel different from the existing designs, considering either a different colour palette in the designs or different motif with the leave design. Any nature based designs should consider the Australian fauna or flora. Also suggest avoiding images in the designs. The principles are not numbered or liner in the concept of how they function. Happy to answer any further questions and thank you for your suggested concepts.

Disaster recovery practitioners, Government agencies , Non-government organisations, Community recovery workers and Community stakeholders and volunteers

Disaster recovery

• Modern, warm, visually engaging, human-centred, Australian in context and different to the current design.
• Symbols for each principles
• Images of disaster destruction, Emergency response imagery, Overly corporate or bureaucratic designs, Designs that focus on deficits rather than recovery and growth, avoid too much black

```html
<!DOCTYPE html>
<html lang="en">
<head>
<meta charset="utf-8">
<title>Harbourline Charter for Community Mending – Brochure</title>
<link href="https://fonts.googleapis.com/css2?family=Montserrat:wght@400;500;600;700;800&family=Overpass:wght@400;500&display=swap" rel="stylesheet">
<style>
  :root{
    --page:#d6dec5;
    --cream:#f7e9c8;
    --peach:#f1cf9c;
    --green:#6a9734;
    --green-light:#a9c97a;
    --green-dark:#2f6b3a;
    --navy:#14385a;
    --title:#141414;
    --text:#2b2b2b;
    --pale-green:#cfdcb3;
    --teal:#127c86;
    --purple:#5a2d82;
    --orange:#e4691b;
    --blue:#1f4e9c;
    --yellow:#efa81e;
    --node-green:#4f7a35;
  }
  *{box-sizing:border-box;margin:0;padding:0}
  html,body{width:896px;height:1200px;overflow:hidden;background:var(--page);font-family:"Montserrat",sans-serif}
  .brochure{position:absolute;left:18px;top:296px;width:860px;height:608px;background:#fff;box-shadow:0 3px 10px rgba(0,0,0,.18);overflow:hidden}
  .panel{position:absolute;top:0;height:100%}
  .panel--cover{left:0;width:287px;background:linear-gradient(180deg,var(--cream) 0%,#f4e2bd 40%,var(--peach) 55%)}
  .panel--partners{left:287px;width:287px;border-right:1px solid #e2e2e2}
  .panel--overview{left:574px;width:286px}

  .eyebrow{font-weight:500;font-size:11px;letter-spacing:.02em;color:var(--title)}
  .cover-title{position:absolute;left:57px;top:44px}
  .title-main{font-family:"Overpass",sans-serif;font-weight:500;font-size:38px;line-height:1;color:var(--title);margin-top:6px}
  .title-accent{font-family:"Overpass",sans-serif;font-weight:500;font-size:38px;line-height:1;color:var(--green)}
  .cover-tagline{position:absolute;left:57px;top:178px;font-weight:700;font-size:11.5px;line-height:1.2;color:var(--green-dark)}
  .cover-photo{position:absolute;left:0;top:310px;width:287px;height:230px;background:linear-gradient(180deg,#e8b679 0%,#b08058 30%,#4a4036 70%,#5b5148 100%)}
  .cover-wave{position:absolute;left:0;bottom:0;width:287px;height:170px}
  .cover-strap{position:absolute;left:56px;top:534px;font-weight:700;font-size:11.5px;line-height:1.2;color:#fff}

  .partner-grid{position:absolute;left:30px;top:60px;width:230px;display:grid;grid-template-columns:1fr 1fr;row-gap:26px;column-gap:8px}
  .partner{display:flex;flex-direction:column;align-items:center;text-align:center;gap:4px;font-weight:600;font-size:7px;line-height:1.2;color:#333}
  .partner-mark{width:30px;height:30px;border-radius:50%;background:#e7e7e7}
  .partner-mark--sq{border-radius:3px}
  .partner--wide{grid-column:1 / span 2;flex-direction:row;justify-content:flex-start;padding-left:18px}
  .partner--wide .partner-mark{width:22px;height:22px}
  .partners-label{position:absolute;left:0;width:287px;top:488px;text-align:center;font-size:8px;letter-spacing:.02em;color:#333}
  .lead-partner{position:absolute;left:70px;top:512px;display:flex;align-items:center;gap:10px;font-size:8.5px;line-height:1.25;color:#333}
  .lead-partner .partner-mark{width:34px;height:34px;background:#bfe8f3}
  .lead-partner small{display:block;font-size:6px;letter-spacing:.12em}

  .green-strip{position:absolute;left:166px;top:0;width:120px;height:100%;background:var(--green)}
  .overview-title{position:absolute;left:22px;top:48px;z-index:2;white-space:nowrap}
  .overview-title .eyebrow{font-size:8px}
  .overview-title .title-main{font-size:15.5px;margin-top:3px}
  .overview-title .title-accent{font-size:15.5px}
  .overview-body{position:absolute;left:24px;top:84px;width:136px;font-size:7.3px;line-height:1.33;color:var(--text)}
  .strip-heading{position:absolute;left:175px;top:134px;width:104px;font-weight:800;font-size:10px;line-height:1.28;color:#fff}
  .strip-body{position:absolute;left:175px;top:195px;width:104px;font-size:7.3px;line-height:1.33;color:#fff}
  .outcomes{position:absolute;right:14px;top:374px;text-align:right;color:#fff;font-size:7.3px;line-height:1.3}
  .outcomes h3{font-weight:800;font-size:10px;line-height:1.25;margin-bottom:12px}
  .outcomes li{list-style:none;margin-bottom:8px}
  .outcomes b{font-weight:700}
  .diagram{position:absolute;left:0;top:340px;width:286px;height:268px}
  .bottom-sweep{position:absolute;left:287px;bottom:0;width:573px;height:110px}
</style>
</head>
<body>
<main class="brochure">

  <section class="panel panel--cover">
    <div class="cover-title">
      <p class="eyebrow">HARBOURLINE CHARTER FOR</p>
      <h1 class="title-main">Community</h1>
      <p class="title-accent">Mending</p>
    </div>
    <p class="cover-tagline">Guiding effective,<br>community centered<br>recovery</p>
    <div class="cover-photo" role="img" aria-label="Photo of three friends seen from behind, sitting on a timber deck watching a sunset over a town"></div>
    <svg class="cover-wave" viewBox="0 0 287 170" preserveAspectRatio="none" aria-hidden="true">
      <defs>
        <linearGradient id="waveFill" x1="0" y1="0" x2="1" y2="1">
          <stop offset="0" stop-color="#6a9734"/>
          <stop offset=".55" stop-color="#3f7a45"/>
          <stop offset="1" stop-color="#14385a"/>
        </linearGradient>
      </defs>
      <path d="M0 30 C60 10 110 70 170 85 C220 98 250 90 287 120 L287 170 L0 170 Z" fill="url(#waveFill)"/>
    </svg>
    <p class="cover-strap">Working together to<br>help communities<br>recover from disaster</p>
  </section>

  <section class="panel panel--partners">
    <div class="partner-grid">
      <div class="partner"><span class="partner-mark"></span>Commonwealth Office<br>of Community Services</div>
      <div class="partner"><span class="partner-mark"></span>Commonwealth Office<br>of Civic Affairs</div>
      <div class="partner"><span class="partner-mark"></span>Southern Cross<br>Aid Society</div>
      <div class="partner"><span class="partner-mark"></span>Gulfland<br>State Office</div>
      <div class="partner"><span class="partner-mark partner-mark--sq"></span>Westcoast<br>State Office</div>
      <div class="partner"><span class="partner-mark partner-mark--sq"></span>Islandvale<br>Government</div>
      <div class="partner"><span class="partner-mark partner-mark--sq"></span>Sunreef<br>State Office</div>
      <div class="partner"><span class="partner-mark"></span>Capital Territory<br>Office</div>
      <div class="partner"><span class="partner-mark"></span>Topend Territory<br>Office</div>
      <div class="partner"><span class="partner-mark partner-mark--sq"></span>Bayside<br>State Office</div>
      <div class="partner partner--wide"><span class="partner-mark partner-mark--sq"></span>Eastcoast Office of<br>Response Planning</div>
    </div>
    <p class="partners-label">PARTNERS IN DEVELOPMENT FROM THE</p>
    <div class="lead-partner"><span class="partner-mark"></span><p>Community Care<br>Advisory Circle<small>AUSTRALIA</small></p></div>
  </section>

  <svg class="bottom-sweep" viewBox="0 0 573 110" preserveAspectRatio="none" aria-hidden="true">
    <path d="M0 60 C30 90 50 110 50 110 L0 110 Z" fill="var(--pale-green)"/>
    <path d="M210 110 C300 70 420 40 573 30 L573 110 Z" fill="var(--pale-green)"/>
  </svg>

  <section class="panel panel--overview">
    <div class="green-strip"></div>
    <div class="overview-title">
      <p class="eyebrow">HARBOURLINE CHARTER FOR</p>
      <h2 class="title-main">Community <span class="title-accent">Mending</span></h2>
    </div>
    <p class="overview-body">Disasters can deeply impact lives and livelihoods. Working with communities recovering from disasters is complex and challenging. These principles are a way to guide our efforts, our approach, our planning and our decision-making.<br>Disaster recovery is part of emergency management, which includes the broader components of prevention, preparedness and response. Planning for recovery is integral to emergency preparation and mitigation actions may often be initiated as part of recovery.<br>Disaster recovery includes built, environmental and economic elements, all contributing to individual and social wellbeing. Recovery can provide an opportunity to improve these aspects beyond previous conditions, contributing to a more resilient community.</p>
    <h3 class="strip-heading">THE<br>RELATIONSHIP<br>BETWEEN<br>THE PRINCIPLES</h3>
    <p class="strip-body">While all the principles are equally critical to ensure effective recovery, understanding the local and broader context and recognising complexity are foundational.<br>The descriptions beneath each principle overleaf provide further guidance for working with communities in disaster recovery</p>

    <div class="outcomes">
      <h3>SUCCESSFUL<br>RECOVERY</h3>
      <ul>
        <li>Understand the<br><b>CONTEXT</b></li>
        <li>Recognise<br><b>COMPLEXITY</b></li>
        <li>Use<br><b>COMMUNITY-LED</b><br>approaches</li>
        <li><b>COORDINATE</b><br>all activities</li>
        <li><b>COMMUNICATE</b><br>effectively</li>
        <li>Recognise and build<br><b>CAPACITY</b></li>
      </ul>
    </div>

    <svg class="diagram" viewBox="0 0 286 268" role="img" aria-label="Six principles arranged in a ring around successful recovery">
      <g transform="translate(0,32)">
        <g fill="none" stroke-width="1.2" stroke-dasharray="1.5 2.5">
          <path d="M102 14 A80 80 0 0 1 171 54" stroke="var(--node-green)"/>
          <path d="M171 54 A80 80 0 0 1 171 134" stroke="var(--teal)"/>
          <path d="M171 134 A80 80 0 0 1 102 174" stroke="var(--purple)"/>
          <path d="M102 174 A80 80 0 0 1 33 134" stroke="var(--orange)"/>
          <path d="M33 134 A80 80 0 0 1 33 54" stroke="var(--blue)"/>
          <path d="M33 54 A80 80 0 0 1 102 14" stroke="var(--yellow)"/>
        </g>
        <g stroke-width="2.2">
          <line x1="102" y1="40" x2="102" y2="52" stroke="var(--node-green)"/>
          <line x1="148" y1="67" x2="136" y2="74" stroke="var(--teal)"/>
          <line x1="148" y1="121" x2="136" y2="114" stroke="var(--purple)"/>
          <line x1="102" y1="148" x2="102" y2="138" stroke="var(--orange)"/>
          <line x1="56" y1="121" x2="68" y2="114" stroke="var(--blue)"/>
          <line x1="56" y1="67" x2="68" y2="74" stroke="var(--yellow)"/>
        </g>
        <g stroke="#fff" stroke-width="1.5">
          <circle cx="102" cy="14" r="26" fill="var(--node-green)"/>
          <circle cx="171" cy="54" r="26" fill="var(--teal)"/>
          <circle cx="171" cy="134" r="26" fill="var(--purple)"/>
          <circle cx="102" cy="174" r="26" fill="var(--orange)"/>
          <circle cx="33" cy="134" r="26" fill="var(--blue)"/>
          <circle cx="33" cy="54" r="26" fill="var(--yellow)"/>
        </g>
        <g fill="#fff" font-family="Montserrat, sans-serif" font-weight="700" font-size="4.6" text-anchor="middle">
          <text x="102" y="18">UNDERSTAND</text><text x="102" y="24">THE CONTEXT</text>
          <text x="171" y="58">RECOGNISE</text><text x="171" y="64">COMPLEXITY</text>
          <text x="171" y="136">USE</text><text x="171" y="142">COMMUNITY-LED</text><text x="171" y="148">APPROACHES</text>
          <text x="102" y="180">COORDINATE</text><text x="102" y="186">ALL ACTIVITIES</text>
          <text x="33" y="138">COMMUNICATE</text><text x="33" y="144">EFFECTIVELY</text>
          <text x="33" y="58">RECOGNISE AND</text><text x="33" y="64">BUILD CAPACITY</text>
        </g>
        <text x="102" y="102" text-anchor="middle" font-family="Montserrat, sans-serif" font-weight="700" font-size="8" fill="var(--navy)">SUCCESSFUL</text>
        <text x="102" y="112" text-anchor="middle" font-family="Montserrat, sans-serif" font-weight="700" font-size="8" fill="var(--green)">RECOVERY</text>
      </g>
    </svg>
  </section>

</main>
</body>
</html>
```